Card Design for my dog training business Brightpaw Obedience

Need a business card design for my dog training business with my new logo. Want the card to come off professional yet fun. Want it to be very eye catchy as well. I normally have these at vet clinics, pet stores, and groomers. so need it to look better than my competitors.
Target Market(s)
dog owners
Industry/Entity Type
Dog Training
Contact Information for Business Card
needs logo, my name and info
Font styles to use
Serif
Colors
0255a3
ffffff
ec1f27
000000
333333
fbfbfb
Requirements
Must have
- Brightpaw Obedience
- Felix Orland
- 415 903 2276
- info@brightpawobedience.example
- www.brightpawobedience.example

```html
<!DOCTYPE html>
<html lang="en">
<head>
<meta charset="utf-8">
<title>Brightpaw Obedience — Business Card</title>
<link href="https://fonts.googleapis.com/css2?family=Tinos&family=Lato:wght@400&display=swap" rel="stylesheet">
<style>
  :root {
    --stage: #999999;
    --card-light: #ffffff;
    --card-dark: #1e1e1e;
    --ink: #1a1a1a;
    --ink-soft: #333333;
    --rule: #555555;
    --mark-light: #cfcfcf;
  }
  * { margin: 0; padding: 0; box-sizing: border-box; }
  html, body { width: 1200px; height: 900px; overflow: hidden; background: var(--stage); }
  .canvas { position: relative; width: 1200px; height: 900px; }

  .card { position: absolute; width: 478px; height: 295px; box-shadow: 2px 4px 6px rgba(0,0,0,0.45); }
  .card--front { left: 120px; top: 275px; background: var(--card-light); border-radius: 0 52px 0 52px; }
  .card--back { left: 606px; top: 273px; background: var(--card-dark); border-radius: 52px 0 52px 0; }

  .brand-name {
    position: absolute;
    font-family: "Tinos", "Times New Roman", serif;
    font-weight: 400;
    font-size: 21px;
    line-height: 1.15;
    text-align: center;
    letter-spacing: 0.5px;
  }
  .card--front .brand-name { left: 28px; top: 120px; width: 160px; color: var(--ink); }
  .card--back .brand-name { left: 0; top: 125px; width: 478px; color: var(--mark-light); }

  .divider { position: absolute; left: 212px; top: 95px; width: 1px; height: 104px; background: var(--rule); }

  .holder-name {
    position: absolute; left: 236px; top: 94px;
    font-family: "Tinos", "Times New Roman", serif;
    font-size: 18px; color: var(--ink); letter-spacing: 0.3px;
    white-space: nowrap;
  }
  .contact-list { position: absolute; left: 235px; top: 145px; list-style: none; }
  .contact-item {
    display: flex; align-items: center; gap: 5px;
    font-family: "Lato", Arial, sans-serif; font-size: 13px; color: var(--ink-soft);
    height: 17.5px; white-space: nowrap;
  }
  .contact-icon { width: 10px; height: 10px; fill: var(--ink); flex: none; }
</style>
</head>
<body>
<div class="canvas">
  <section class="card card--front">
    <div class="brand-name">Brightpaw<br>Obedience</div>
    <div class="divider"></div>
    <div class="holder-name">FELIX ORLAND</div>
    <ul class="contact-list">
      <li class="contact-item">
        <svg class="contact-icon" viewBox="0 0 10 10"><path d="M1 3.5 Q5 0.5 9 3.5 L8 5 L6.5 4 L6.5 3 Q5 2.5 3.5 3 L3.5 4 L2 5 Z M2.5 5.5 L7.5 5.5 L8.5 9 L1.5 9 Z"/></svg>
        415 903 2276
      </li>
      <li class="contact-item">
        <svg class="contact-icon" viewBox="0 0 10 10"><path d="M0.5 2 H9.5 V8.5 H0.5 Z" /><path d="M0.8 2.3 L5 5.6 L9.2 2.3" stroke="#fff" stroke-width="0.9" fill="none"/></svg>
        info@brightpawobedience.example
      </li>
      <li class="contact-item">
        <svg class="contact-icon" viewBox="0 0 10 10"><circle cx="5" cy="5" r="4.5"/><path d="M5 0.5 V9.5 M0.5 5 H9.5 M5 0.5 Q2 5 5 9.5 M5 0.5 Q8 5 5 9.5" stroke="#fff" stroke-width="0.6" fill="none"/></svg>
        www.brightpawobedience.example
      </li>
    </ul>
  </section>

  <section class="card card--back">
    <div class="brand-name">Brightpaw<br>Obedience</div>
  </section>
</div>
</body>
</html>
```